Stated Income Loans

Flyer design to be used on social media platforms (i.e. Facebook, Instagram etc.)

Target Market(s)

Real Estate Investors

Requirements
Must have
• INVESTOR STATED INCOME LOANS
• "IT'S TIME TO THINK BIG"
• * Purchase or Refinance up to 3 Million
• * No Income Docs or Bank Statements
• * Vacant Properties Allowed
• * Minimum Credit Score 620
• * Cash Out up to 80%
• Same Day Pre-Approval
• 20-30 Day Close
• Call Marcus Delvane today...
• Brightkeel Lending Group, Inc.
• Phone (800) 416-9027 x 42
• Direct (240) 958-2046
• www.brightkeelhub.com
• NMLS #386710 / #57483
Should not have
• Do not use same color scheme as website. Be creative.

```html
<!DOCTYPE html>
<html lang="en">
<head>
<meta charset="utf-8">
<title>Investor Stated Income Loans – Flyers</title>
<link href="https://fonts.googleapis.com/css2?family=Jost:wght@300;400;500;600;700;800&display=swap" rel="stylesheet">
<style>
  :root{
    --olive:#5a7a1c;
    --olive-dark:#46611a;
    --navy:#0e4a6a;
    --navy-dark:#0a3a55;
    --paper:#f3f3f1;
    --ink:#222;
    --bg-left:#f3f8dc;
    --bg-right:#c6e9f7;
  }
  *{box-sizing:border-box;margin:0;padding:0}
  html,body{width:1200px;height:720px;overflow:hidden}
  body{font-family:"Jost",sans-serif;color:var(--ink);
    background:linear-gradient(90deg,var(--bg-left) 0 50%,var(--bg-right) 50% 100%);position:relative}
  .flyer{position:absolute;top:28px;width:480px;height:664px;background:var(--paper);
    box-shadow:0 10px 30px rgba(0,0,0,.18);overflow:hidden}
  .flyer--green{left:60px;--accent:var(--olive);--accent-dark:var(--olive-dark)}
  .flyer--blue{left:660px;--accent:var(--navy);--accent-dark:var(--navy-dark)}
  .flyer__header{position:absolute;left:0;top:0;width:100%;height:62px;background:var(--accent);
    display:flex;align-items:center;justify-content:center}
  .flyer__title{color:#fff;font-weight:700;font-size:25px;letter-spacing:.3px}
  .hero{position:absolute;left:0;top:62px;width:100%;height:250px}
  .hero__photo{position:absolute;inset:0;width:100%;height:100%}
  .headline{position:absolute;color:#fff;line-height:.95}
  .headline__small{font-weight:300;font-size:34px;display:block}
  .headline__big{font-weight:800;font-size:40px;display:block;margin-top:4px}
  .flyer--green .headline-box{position:absolute;left:0;top:92px;width:240px;height:130px;background:rgba(90,122,28,.75)}
  .flyer--green .headline{left:18px;top:102px}
  .flyer--blue .headline-box{position:absolute;left:0;top:86px;width:262px;height:136px;background:var(--navy)}
  .flyer--blue .headline{left:22px;top:96px}

  /* feature icons */
  .features{position:absolute;left:0;top:320px;width:100%;height:200px}
  .feature{position:absolute;width:110px;text-align:center;font-size:10.5px;line-height:1.15;color:#333}
  .feature svg{display:block;margin:0 auto 6px;width:46px;height:46px;stroke:var(--accent);fill:none;stroke-width:2;stroke-linecap:round;stroke-linejoin:round}

  /* checklist */
  .checklist{position:absolute;left:32px;top:324px;list-style:none}
  .checklist li{display:flex;align-items:center;height:27px;font-size:15px;color:#333;white-space:nowrap}
  .checklist svg{width:16px;height:16px;margin-right:12px;stroke:var(--navy);fill:none;stroke-width:2;stroke-linecap:round;stroke-linejoin:round;flex:none}
  .checklist em{font-style:normal;color:var(--navy);font-weight:500;margin-left:5px}
  .checklist .em-lg{font-size:19px}
  .money-photo{position:absolute;left:250px;top:340px;width:230px;height:180px}

  /* contact block */
  .contact{position:absolute;left:0;top:528px;width:100%;height:100px}
  .contact__band{position:absolute;left:0;top:22px;width:458px;height:78px;background:var(--accent)}
  .brand-card{position:absolute;left:22px;top:0;width:178px;height:96px;background:#fff;
    box-shadow:0 3px 10px rgba(0,0,0,.25);display:flex;align-items:center;justify-content:center;gap:8px;padding:0 10px}
  .brand-card__mark{width:14px;height:14px;border-radius:50%;background:var(--accent);flex:none}
  .brand-card__name{font-weight:600;font-size:13px;line-height:1.2;color:var(--accent)}
  .contact__call{position:absolute;left:214px;top:0;font-size:13px;color:#222;white-space:nowrap}
  .contact__call strong{color:var(--accent);font-weight:600}
  .contact__details{position:absolute;left:214px;top:30px;font-size:11px;line-height:1.4;color:#fff;white-space:nowrap}
  .contact__portrait{position:absolute;left:378px;top:24px;width:80px;height:76px}

  .social{position:absolute;left:0;bottom:10px;width:100%;display:flex;justify-content:center;gap:8px}
  .social span{width:16px;height:16px;border:1.5px solid var(--accent);border-radius:50%}
</style>
</head>
<body>

<section class="flyer flyer--green">
  <header class="flyer__header"><h1 class="flyer__title">INVESTOR STATED INCOME LOANS</h1></header>
  <div class="hero">
    <svg class="hero__photo" role="img" aria-label="Black and white photo of people silhouetted at a window overlooking a city skyline" viewBox="0 0 480 250" preserveAspectRatio="none">
      <defs><linearGradient id="g-hero" x1="0" y1="0" x2="0" y2="1"><stop offset="0" stop-color="#6d6d6d"/><stop offset=".5" stop-color="#a7a7a7"/><stop offset="1" stop-color="#2a2a2a"/></linearGradient></defs>
      <polygon points="0,0 480,0 480,250 0,222" fill="url(#g-hero)"/>
    </svg>
    <div class="headline-box"></div>
    <p class="headline"><span class="headline__small">It's</span><span class="headline__small">TIME To</span><span class="headline__big">THINK BIG</span></p>
  </div>
  <div class="features">
    <div class="feature" style="left:12px;top:0">
      <svg viewBox="0 0 48 48"><circle cx="24" cy="24" r="14"/><path d="M24 15v18M28 19c-1-2-7-2-7 1s7 2 7 5-6 3-7 1"/><path d="M8 20a16 16 0 0 1 26-10M40 28a16 16 0 0 1-26 10"/></svg>
      Purchase or Refinance<br>up to 3 Million</div>
    <div class="feature" style="left:124px;top:8px">
      <svg viewBox="0 0 48 48"><path d="M12 4h20l6 6v34H12z"/><path d="M25 12v14M28 15c-1-2-6-2-6 1s6 2 6 5-5 3-6 1M17 32h16M17 37h16"/></svg>
      No Income Docs or<br>Bank Statements</div>
    <div class="feature" style="left:236px;top:18px">
      <svg viewBox="0 0 48 48"><path d="M6 22L24 8l18 14M10 20v22h28V20M18 42V30h12v12M14 26h4M30 26h4"/></svg>
      Vacant Properties<br>Allowed</div>
    <div class="feature" style="left:350px;top:40px">
      <svg viewBox="0 0 48 48"><rect x="6" y="14" width="34" height="22" rx="3" transform="rotate(-20 23 25)"/><path d="M10 24l30-11M14 34l8-3"/></svg>
      Minimum Credit<br>Score 620</div>
    <div class="feature" style="left:56px;top:104px">
      <svg viewBox="0 0 48 48"><rect x="4" y="14" width="28" height="18" rx="2"/><circle cx="18" cy="23" r="5"/><ellipse cx="37" cy="28" rx="8" ry="3"/><path d="M29 28v10c0 2 16 2 16 0V28M29 33c0 2 16 2 16 0"/></svg>
      Cash Out up to 80%</div>
    <div class="feature" style="left:180px;top:114px">
      <svg viewBox="0 0 48 48"><rect x="8" y="8" width="26" height="34" rx="2"/><path d="M13 17l3 3 5-5M13 27l3 3 5-5M25 18h5M25 28h5M42 14L28 38l-3 4 1-5 14-24z"/></svg>
      Same Day Pre-Approval</div>
    <div class="feature" style="left:300px;top:132px">
      <svg viewBox="0 0 48 48"><rect x="6" y="10" width="32" height="30" rx="2"/><path d="M6 18h32M13 6v8M31 6v8M12 25h4M20 25h4M28 25h4M12 32h4"/><circle cx="36" cy="36" r="7"/><path d="M33 36l2 2 4-4"/></svg>
      20-30 Day Close</div>
  </div>
  <div class="contact">
    <div class="contact__band"></div>
    <div class="brand-card"><span class="brand-card__mark"></span><span class="brand-card__name">Brightkeel Lending<br>Group, Inc.</span></div>
    <p class="contact__call">Call <strong>Marcus Delvane</strong> today...</p>
    <p class="contact__details">Phone: (800) 416-9027 x 42<br>Direct: (240) 958-2046<br>www.brightkeelhub.com<br>NMLS #386710 / #57483</p>
    <svg class="contact__portrait" role="img" aria-label="Portrait photo of the loan officer in a dark suit" viewBox="0 0 80 76" preserveAspectRatio="none">
      <defs><linearGradient id="g-port1" x1="0" y1="0" x2="0" y2="1"><stop offset="0" stop-color="#7a5a48"/><stop offset="1" stop-color="#1d1d22"/></linearGradient></defs>
      <rect width="80" height="76" fill="url(#g-port1)"/>
    </svg>
  </div>
  <div class="social"><span></span><span></span><span></span></div>
</section>

<section class="flyer flyer--blue">
  <header class="flyer__header"><h1 class="flyer__title">INVESTOR STATED INCOME LOANS</h1></header>
  <div class="hero">
    <svg class="hero__photo" role="img" aria-label="Black and white photo looking up at glass skyscrapers against a cloudy sky" viewBox="0 0 480 250" preserveAspectRatio="none">
      <defs><linearGradient id="g-sky" x1="0" y1="0" x2="1" y2="1"><stop offset="0" stop-color="#3a3a3a"/><stop offset=".45" stop-color="#c9c9c9"/><stop offset="1" stop-color="#2b2b2b"/></linearGradient></defs>
      <polygon points="0,0 480,0 480,250 0,232" fill="url(#g-sky)"/>
    </svg>
    <div class="headline-box"></div>
    <p class="headline"><span class="headline__small">It's</span><span class="headline__small">TIME To</span><span class="headline__big">THINK BIG</span></p>
  </div>
  <svg class="money-photo" role="img" aria-label="Black and white photo of a rolled bundle of banknotes" viewBox="0 0 230 180" preserveAspectRatio="none">
    <defs><linearGradient id="g-money" x1="0" y1="0" x2="1" y2="1"><stop offset="0" stop-color="#9a9a9a"/><stop offset=".6" stop-color="#4a4a4a"/><stop offset="1" stop-color="#141414"/></linearGradient></defs>
    <polygon points="120,0 230,0 230,180 0,180" fill="url(#g-money)"/>
    <polygon points="112,0 122,0 2,180 -8,180" fill="var(--navy)"/>
  </svg>
  <ul class="checklist">
    <li><svg viewBox="0 0 16 16"><circle cx="8" cy="8" r="6.5"/><path d="M5 8l2 2 5-5"/></svg>Purchase or Refinance up to<em class="em-lg">3 Million</em></li>
    <li><svg viewBox="0 0 16 16"><circle cx="8" cy="8" r="6.5"/><path d="M5 8l2 2 5-5"/></svg><em style="margin:0 5px 0 0">No</em>Income Docs or Bank Statements</li>
    <li><svg viewBox="0 0 16 16"><circle cx="8" cy="8" r="6.5"/><path d="M5 8l2 2 5-5"/></svg>Vacant Properties Allowed</li>
    <li><svg viewBox="0 0 16 16"><circle cx="8" cy="8" r="6.5"/><path d="M5 8l2 2 5-5"/></svg>Minimum Credit Score<em class="em-lg">620</em></li>
    <li><svg viewBox="0 0 16 16"><circle cx="8" cy="8" r="6.5"/><path d="M5 8l2 2 5-5"/></svg>Cash Out up to<em class="em-lg">80%</em></li>
    <li><svg viewBox="0 0 16 16"><circle cx="8" cy="8" r="6.5"/><path d="M5 8l2 2 5-5"/></svg>Same Day<em>Pre-Approval</em></li>
    <li><svg viewBox="0 0 16 16"><circle cx="8" cy="8" r="6.5"/><path d="M5 8l2 2 5-5"/></svg><em class="em-lg" style="margin:0 5px 0 0">20-30</em>Day Close</li>
  </ul>
  <div class="contact">
    <div class="contact__band"></div>
    <div class="brand-card"><span class="brand-card__mark"></span><span class="brand-card__name">Brightkeel Lending<br>Group, Inc.</span></div>
    <p class="contact__call">Call <strong>Marcus Delvane</strong> today...</p>
    <p class="contact__details">Phone: (800) 416-9027 x 42<br>Direct: (240) 958-2046<br>www.brightkeelhub.com<br>NMLS #386710 / #57483</p>
    <svg class="contact__portrait" role="img" aria-label="Portrait photo of the loan officer in a dark suit" viewBox="0 0 80 76" preserveAspectRatio="none">
      <defs><linearGradient id="g-port2" x1="0" y1="0" x2="0" y2="1"><stop offset="0" stop-color="#7a5a48"/><stop offset="1" stop-color="#1d1d22"/></linearGradient></defs>
      <rect width="80" height="76" fill="url(#g-port2)"/>
    </svg>
  </div>
  <div class="social"><span></span><span></span><span></span></div>
</section>

</body>
</html>
```